High Tech Real Estate Startup needs a business card

We are developing an innovative real estate marketing product based around advanced search and virtual reality.

We talk to people, we need business cards.

Target Market(s)

The target market is technology professionals and realtors.

Contact Information for Business Card

The information to be included will include

Name
Title
Phone Number
E-mail Address
www.zelquin.com

It should use simple iconography for each one of those fields.

Font styles to use
Other font styles liked:
• Co, Jubilat, Avenir

Colors

Designer to choose colors to be used in the design.

Requirements
Must have
• Clean aesthetic,
• Good use of negative space.
• It should use our company logo, shown in the attached file. It is able to use the negative of that logo (coloured font and white background) and I have attached other acceptable accent colours in a swatch file.
Should not have
• Should not be too busy
• No extraneous text (slogans, tag lines etc)

```html
<!DOCTYPE html>
<html lang="en">
<head>
<meta charset="UTF-8">
<title>Zelquin Business Card</title>
<link rel="stylesheet" href="https://fonts.googleapis.com/css2?family=Montserrat:wght@500&family=Lato:wght@400;700&display=swap">
<style>
  :root {
    --teal: #00b9be;
    --card-white: #ffffff;
    --backdrop: #ecefef;
    --text-light: #ffffff;
  }
  html, body {
    margin: 0;
    padding: 0;
    width: 1200px;
    height: 900px;
    overflow: hidden;
    background: var(--backdrop);
  }
  .canvas {
    position: relative;
    width: 1200px;
    height: 900px;
  }
  .business-card {
    position: absolute;
    left: 160px;
    top: 178px;
    width: 880px;
    height: 543px;
    background: var(--card-white);
    box-shadow: 0 6px 24px rgba(0, 0, 0, 0.08);
    overflow: hidden;
  }
  .brand-area {
    position: absolute;
    left: 0;
    top: 0;
    width: 100%;
    height: 320px;
    display: flex;
    align-items: center;
    justify-content: center;
  }
  .brand-name {
    font-family: "Montserrat", sans-serif;
    font-weight: 500;
    font-size: 100px;
    letter-spacing: 4px;
    color: var(--teal);
    margin: 0;
    line-height: 1;
    padding-top: 20px;
  }
  .contact-band {
    position: absolute;
    left: 0;
    top: 320px;
    width: 100%;
    height: 223px;
    background: var(--teal);
    color: var(--text-light);
  }
  .person {
    position: absolute;
    right: 464px;
    top: 82px;
    text-align: right;
    font-family: "Lato", sans-serif;
  }
  .person-name {
    font-weight: 700;
    font-size: 28px;
    letter-spacing: 0.3px;
    margin: 0;
    line-height: 1.2;
  }
  .person-title {
    font-weight: 400;
    font-size: 22px;
    margin: 4px 0 0;
    line-height: 1.2;
  }
  .divider {
    position: absolute;
    left: 439px;
    top: 77px;
    width: 2px;
    height: 82px;
    background: var(--text-light);
  }
  .contact-list {
    position: absolute;
    left: 460px;
    top: 68px;
    margin: 0;
    padding: 0;
    list-style: none;
    font-family: "Lato", sans-serif;
    font-size: 23px;
  }
  .contact-item {
    display: flex;
    align-items: center;
    height: 32px;
  }
  .contact-icon {
    width: 16px;
    height: 16px;
    margin-right: 11px;
    fill: var(--text-light);
    flex: none;
  }
</style>
</head>
<body>
<div class="canvas">
  <div class="business-card">
    <div class="brand-area">
      <p class="brand-name">ZELQUIN</p>
    </div>
    <div class="contact-band">
      <div class="person">
        <p class="person-name">DANIEL HARTWELL</p>
        <p class="person-title">Managing Director</p>
      </div>
      <div class="divider"></div>
      <ul class="contact-list">
        <li class="contact-item">
          <svg class="contact-icon" viewBox="0 0 16 16" aria-hidden="true">
            <path d="M3.6 1.2l2.3 2.6c.4.4.3 1-.1 1.4L4.7 6.3c.9 2 2.9 4 5 5l1.1-1.1c.4-.4 1-.5 1.4-.1l2.6 2.3c.4.4.4 1 0 1.4l-1.3 1.3C12 16.6 9 15.6 5.7 12.3 2.4 9 1.4 6 2.9 4.4l1.3-1.3c-.1 0 .1-.3.1-.3z"/>
          </svg>
          <span>(044)987654321</span>
        </li>
        <li class="contact-item">
          <svg class="contact-icon" viewBox="0 0 16 16" aria-hidden="true">
            <path d="M1 3h14v1.2L8 8.6 1 4.2z"/>
            <path d="M1 5.6l7 4.4 7-4.4V13H1z"/>
          </svg>
          <span>info@zelquin.com</span>
        </li>
        <li class="contact-item">
          <svg class="contact-icon" viewBox="0 0 16 16" aria-hidden="true">
            <circle cx="8" cy="8" r="7"/>
            <path d="M4.5 4.5c1.5.2 2.2 1 2 2.2-.3 1.3-1.8 1.2-1.8 2.6 0 1 .8 1.6.8 3" fill="none" stroke="#00b9be" stroke-width="1.3"/>
            <path d="M10 2.6c-.4 1.2.5 1.8 1.4 2.2 1 .5.8 1.8 2 2" fill="none" stroke="#00b9be" stroke-width="1.3"/>
          </svg>
          <span>www.zelquin.com</span>
        </li>
      </ul>
    </div>
  </div>
</div>
</body>
</html>
```